Bluefern Business Services needs a new interactive and interesting website

We need an interesting, professional, modern and functional company website for Bluefern Business Services - a young IT Services company based out of Chennai, India.

Bluefern Business Services is a fully owned subsidiary of Marlow Goods, one of the world's leading direct to consumer wine merchant.

We already have a registered company logo which must feature in the website.

We conceive, design, develop, test, implement and support IT solutions across the entire Marlow Goods IT landscape. For ex : We currently run about 25 e-commerce websites for Marlow Goods on ATG and Dot Net.

We would like to see our corporate colors used in the website. (Burgundy wine and wine green - source: www.bluefernbs-site.com)

We are looking at this website to communicate a fun, friendly and professionally managed company - reaching out to career seekers, prospective customers and general public.

For reference - The company name 'Bluefern' is an inspiration from the Marlow Goods lineage.

The second image with the world map is stickered on our main entrance to the office, I am not sure where this can be used -just putting it out there..

Please note that there are only a few more days to submit designs for this contest  !

I would appreciate if you can help posting your designs in time for our review and consideration.

Thanks.

Reason: Thanks for your inputs. We have a number of designers and a lot to digest and work with in the past few days. There has been a rush of new designs in the last few days Hence we will require more time to process these and make our decision. Hence i am requesting the contest to be open for more days. Regards, Tarun

Target Market(s)

Prospective job seekers who want to know more about the company and also wish to apply for a job vacancy
People wanting to know more about the company in general and our progress
People who want to see what we offer and how we can help them too - prospective customers
Companies that are interested in our IT Captive journey and are looking for a business opportunity

Industry/Entity Type

E-Commerce

Requirements
Must have
• Log In/ Register facility acting as a Single Sign on for Intranet (Employees)

Facility to post job vacancies (with an expiry date) and enable people to apply for a role and upload their CV/Resume.

Facility to Review Job applications

Facility for website visitors to contact Bluefern business Services via an online 'Contact Us' form with a split of job seekers and business opportunities

Gallery facility to upload pictures regarding company events
Nice to have
• Less Cluttered and contemporary design
Some Wine/Vineyard inspirations will be good but not too much, the company is an IT services company

```html
<!DOCTYPE html>
<html lang="en">
<head>
<meta charset="utf-8">
<title>Bluefern Business Services</title>
<link href="https://fonts.googleapis.com/css2?family=Arimo:wght@400;700&family=Open+Sans:wght@400;600&display=swap" rel="stylesheet">
<style>
:root{
  --wine:#8a1247;
  --wine-dark:#6e0c38;
  --wine-soft:#a54574;
  --ink:#333;
  --muted:#666;
  --line:#dcdcdc;
  --bg:#fff;
  --band:#f4f4f5;
}
*{margin:0;padding:0;box-sizing:border-box}
html,body{width:818px;height:1200px;overflow:hidden;background:var(--bg)}
body{position:relative;font-family:"Arimo",Arial,sans-serif;color:var(--ink)}
.abs{position:absolute}
.topbar{left:0;top:0;width:818px;height:24px;background:#fafafa;border-bottom:1px solid #e6e6e6}
.topbar .contact{left:137px;top:8px;font-size:6px;color:#999;display:flex;gap:8px}
.topbar .social{left:565px;top:5px;display:flex;gap:2px}
.topbar .social span{width:12px;height:12px;border:1px solid #ccc;background:#fff}
.header{left:0;top:24px;width:818px;height:58px;background:var(--wine)}
.brand{left:136px;top:34px;color:#fff;display:flex;gap:5px;align-items:flex-start;white-space:nowrap}
.brand .dot{width:14px;height:14px;border-radius:50%;background:#fff;margin-top:4px}
.brand b{display:block;font-size:22px;line-height:22px;font-weight:700;letter-spacing:-.5px}
.brand small{display:block;font-size:12px;line-height:14px;margin-left:21px;margin-top:-2px}
.nav{left:405px;top:24px;height:58px;display:flex;font-size:7px;font-weight:700;color:#fff}
.nav a{display:block;padding:26px 8px 0;height:58px;color:#fff;text-decoration:none}
.nav a.active{background:var(--wine-soft);border-bottom:3px solid #c07a9c}
.hero{left:0;top:82px;width:818px;height:230px;background:linear-gradient(90deg,#d6d7da 0%,#eef0f2 40%,#f3f3f4 62%,#6c2a37 66%,#8a3a44 85%,#5c1e2a 100%)}
.hero .photo{left:0;top:0;width:818px;height:230px}
.arrow{width:36px;height:38px;background:#444;display:flex;align-items:center;justify-content:center}
h2{font-weight:400;font-size:14px;color:var(--wine)}
h3.sec{font-weight:400;font-size:14px;color:#333}
p.small{font-size:5.8px;line-height:13px;color:#555}
.more{font-size:6.5px;color:var(--wine)}
.welcome-img{left:456px;top:324px;width:225px;height:96px;background:linear-gradient(90deg,#dfe6ec,#cfd5db 50%,#c9b8a8);border:1px solid #ccc}
.card{width:127px;height:117px;border:1px solid var(--line);background:#fff;text-align:center}
.card .icon{width:26px;height:26px;margin:8px auto 0;border-radius:3px}
.card h4{font-size:6.4px;line-height:10px;color:var(--wine);margin-top:14px;height:22px;font-weight:700}
.card p{font-size:5.8px;line-height:10px;color:#666;padding:0 6px}
.card .btn{display:inline-block;margin-top:4px;width:62px;height:15px;border:1px solid var(--line);font-size:6.3px;line-height:14px;color:var(--wine)}
.pager{display:flex;gap:3px}
.pager span{width:14px;height:13px;border:1px solid #ccc;background:#fff;display:flex;align-items:center;justify-content:center}
.event-img{width:164px;height:91px;border:1px solid #ccc}
.event h4{font-size:9.5px;font-weight:400;color:var(--wine)}
.redbtn{display:inline-block;background:var(--wine);color:#fff;font-size:6px;padding:0 7px;height:19px;line-height:19px}
.opps{left:495px;top:686px;width:186px;height:175px;border:1px solid var(--line);background:#fff}
.opp{height:58px;border-bottom:1px solid var(--line);padding:8px 7px 0;font-size:5.8px;line-height:10px;color:#555;position:relative}
.opp:last-child{border-bottom:0}
.opp .meta{display:flex;justify-content:space-between;margin-top:3px;color:#222}
.opp .meta em{font-style:normal;color:var(--wine);margin-right:22px}
.clients{left:136px;top:909px;width:546px;height:60px;border:1px solid var(--line);background:#fff;display:flex;align-items:center;justify-content:space-around;font-size:9px;color:var(--wine-dark)}
.footer-line{left:0;top:977px;width:818px;height:3px;background:var(--wine)}
.foot{font-family:"Open Sans",Arial,sans-serif}
.foot h5{font-size:7.5px;font-weight:400;color:#444;letter-spacing:.3px}
.foot p,.foot li{font-size:6.2px;line-height:12px;color:#666}
.foot ul{list-style:none;margin-top:12px;width:124px}
.foot li{height:23px;padding-top:2px;border-bottom:1px solid #eee;color:#333}
.fbrand{left:136px;top:1000px;width:105px;height:34px;background:var(--wine);color:#fff;padding:3px 4px;display:flex;gap:3px;white-space:nowrap;overflow:hidden}
.fbrand .dot{width:10px;height:10px;border-radius:50%;background:#fff;margin-top:3px;flex:none}
.fbrand b{display:block;font-size:15px;line-height:15px;font-family:"Arimo",Arial,sans-serif}
.fbrand small{display:block;font-size:8.5px;line-height:11px;margin-left:6px;font-family:"Arimo",Arial,sans-serif}
.fsocial{left:136px;top:1105px;display:flex;gap:4px}
.fsocial span{width:13px;height:13px;border-radius:50%;background:#aaa}
.input{width:70px;height:18px;border:1px solid #ccc;font-size:6px;color:#999;padding:5px 8px}
.signup{width:40px;height:18px;border:1px solid #ccc;font-size:7px;text-align:center;line-height:16px;color:#333}
.bottom{left:0;top:1163px;width:818px;height:37px;background:var(--wine);color:#fff;font-size:6px;text-align:center;line-height:37px}
.green{color:#7cb342}
</style>
</head>
<body>

<div class="abs topbar">
  <div class="abs contact"><span>⌂ 12 Orchard Lane, Elm Town</span><span>✆ +100 555 0142</span><span>● hello@bluefern-mail.test</span></div>
  <div class="abs social"><span></span><span></span><span></span><span></span><span></span><span></span><span></span><span></span></div>
</div>

<header class="abs header"></header>
<div class="abs brand"><span class="dot"></span><div><b>bluefern</b><small>Business Services</small></div></div>
<nav class="abs nav">
  <a class="active">Home</a><a>About Us</a><a>Clients</a><a>Services</a><a>Careers</a><a>Contact Us</a>
</nav>

<section class="abs hero">
  <div class="abs photo" role="img" aria-label="Smiling team of five office workers pointing forward, beside a wine barrel, bottles and grapes"></div>
  <div class="abs arrow" style="left:0;top:94px"><svg width="10" height="14"><path d="M8 1L2 7l6 6" stroke="#fff" stroke-width="2.5" fill="none"/></svg></div>
  <div class="abs arrow" style="left:790px;top:94px;width:28px"><svg width="10" height="14"><path d="M2 1l6 6-6 6" stroke="#fff" stroke-width="2.5" fill="none"/></svg></div>
</section>

<div class="abs" style="left:136px;top:326px;width:310px">
  <h2>Welcome Bluefern Business Services</h2>
  <div style="font-size:10px;margin-top:6px;color:#222">Delivering IT Excellence</div>
  <p class="small" style="margin-top:6px">Welcome to Bluefern Business Services, an emerging provider of global IT consulting and software services. We are part of the Marlow Goods group, a family run business and the world's largest multi-channel home delivery wine merchant...</p>
  <div class="more" style="margin-top:3px">Read More +</div>
</div>
<div class="abs welcome-img" role="img" aria-label="Colleagues reviewing a chart on a glass board"></div>

<div class="abs" style="left:136px;top:440px;width:546px">
  <h3 class="sec">Services</h3>
  <p class="small" style="margin-top:4px">The services we provide enable the businesses we support to efficiently manage key functions, including order management (encompassing e-commerce websites, inbound and outbound call centre operations), order fulfilment, procurement, planning &amp; forecasting, warehouse management operations, financial management, global compliance and risk.</p>
  <div class="more" style="margin-top:3px">Read More +</div>
</div>

<div class="abs card" style="left:136px;top:510px">
  <div class="icon" role="img" aria-label="Application box icon" style="background:linear-gradient(135deg,#6fb24a,#e0b030,#4a7fc0)"></div>
  <h4>Packaged Applications</h4>
  <p>Lorem ipsum dolor sit amet, consectetur adipiscing elit. Nulla convallis</p>
  <span class="btn">Read More</span>
</div>
<div class="abs card" style="left:274px;top:510px">
  <div class="icon" role="img" aria-label="Puzzle pieces icon" style="background:linear-gradient(90deg,#e8c020,#d23030,#3060c0);height:14px;margin-top:14px"></div>
  <h4 style="margin-top:14px">Enterprise Application<br>Integration</h4>
  <p>Lorem ipsum dolor sit amet, consectetur adipiscing elit. Nulla convallis</p>
  <span class="btn">Read More</span>
</div>
<div class="abs card" style="left:414px;top:510px">
  <svg class="icon" width="26" height="26" viewBox="0 0 26 26"><path d="M2 4h4l3 12h12l3-9H8" stroke="#555" stroke-width="1.6" fill="none"/><circle cx="10" cy="21" r="2" fill="#555"/><circle cx="19" cy="21" r="2" fill="#555"/></svg>
  <h4>Digital Commerce</h4>
  <p>Lorem ipsum dolor sit amet, consectetur adipiscing elit. Nulla convallis</p>
  <span class="btn">Read More</span>
</div>
<div class="abs card" style="left:554px;top:510px">
  <svg class="icon" width="26" height="26" viewBox="0 0 26 26"><rect x="2" y="3" width="20" height="16" rx="1" fill="#3a6fb0"/><rect x="4" y="7" width="16" height="10" fill="#fff"/><circle cx="16" cy="15" r="5" fill="none" stroke="#333" stroke-width="1.5"/><path d="M19.5 18.5l4 4" stroke="#333" stroke-width="2"/></svg>
  <h4>Application Development &amp;<br>Maintenance</h4>
  <p>Lorem ipsum dolor sit amet, consectetur adipiscing elit. Nulla convallis</p>
  <span class="btn">Read More</span>
</div>

<div class="abs" style="left:0;top:650px;width:818px;height:212px;background:var(--band)"></div>

<h3 class="abs sec" style="left:136px;top:658px">Events</h3>
<div class="abs pager" style="left:444px;top:662px"><span><svg width="5" height="7"><path d="M4 1L1 3.5 4 6" stroke="#666" fill="none"/></svg></span><span><svg width="5" height="7"><path d="M1 1l3 2.5L1 6" stroke="#666" fill="none"/></svg></span></div>

<div class="abs event" style="left:137px;top:690px;width:164px">
  <div class="event-img" role="img" aria-label="Wine bottles and glasses against a vineyard sunset" style="background:linear-gradient(90deg,#3a2418,#7a6a3a 50%,#a89a6a)"></div>
  <h4 style="margin-top:7px">Party Events</h4>
  <p class="small" style="line-height:10px;margin-top:4px">Lorem ipsum dolor sit amet, consectetur adipiscing elit. Integer sem dui, molestie vitae ornare tincidunt, semper non metus.</p>
  <span class="redbtn" style="margin-top:4px">Read More..</span>
</div>
<div class="abs event" style="left:313px;top:690px;width:164px">
  <div class="event-img" role="img" aria-label="Video of a cheering office crowd" style="background:linear-gradient(160deg,#6a5048,#b08070 50%,#4a3838);position:relative">
    <div class="abs" style="left:0;bottom:0;width:162px;height:12px;background:#111;color:#fff;font-size:5px;line-height:12px;padding-left:4px">00:25 <span style="display:inline-block;width:100px;height:4px;background:#666;vertical-align:middle;margin-left:4px"></span></div>
  </div>
  <h4 style="margin-top:7px">Workplace Social</h4>
  <p class="small" style="line-height:10px;margin-top:4px">Lorem ipsum dolor sit amet, consectetur adipiscing elit. Integer sem dui, molestie vitae ornare tincidunt, semper non metus.</p>
  <span class="redbtn" style="margin-top:4px">Read More..</span>
</div>

<h2 class="abs" style="left:495px;top:661px;color:var(--wine)">Latest opportunities</h2>
<div class="abs pager" style="left:649px;top:662px"><span><svg width="5" height="7"><path d="M4 1L1 3.5 4 6" stroke="#666" fill="none"/></svg></span><span><svg width="5" height="7"><path d="M1 1l3 2.5L1 6" stroke="#666" fill="none"/></svg></span></div>
<div class="abs opps">
  <div class="opp">Lorem ipsum dolor sit amet, consectetur adipiscing elit. Donec sit amet turpis erat. Aenean hendrerit fermentum aliquet.<div class="meta"><span>26/11/2013</span><em>Read More..</em></div></div>
  <div class="opp">Lorem ipsum dolor sit amet, consectetur adipiscing elit. Donec sit amet turpis erat. Aenean hendrerit fermentum aliquet.<div class="meta"><span>26/11/2013</span><em>Read More..</em></div></div>
  <div class="opp">Lorem ipsum dolor sit amet, consectetur adipiscing elit. Donec sit amet turpis erat. Aenean hendrerit fermentum aliquet.<div class="meta"><span>26/11/2013</span><em>Read More..</em></div></div>
</div>

<h3 class="abs sec" style="left:136px;top:883px">Clients</h3>
<div class="abs pager" style="left:649px;top:884px"><span><svg width="5" height="7"><path d="M4 1L1 3.5 4 6" stroke="#666" fill="none"/></svg></span><span><svg width="5" height="7"><path d="M1 1l3 2.5L1 6" stroke="#666" fill="none"/></svg></span></div>
<div class="abs clients">
  <span>Hollowbrook Wine</span><span>Kestrel Wines</span><span>Daily Ledger Wine</span><span>Weekend Gazette Wine Club</span><span>Rovel Wine</span>
</div>

<div class="abs footer-line"></div>

<div class="abs fbrand"><span class="dot"></span><div><b>bluefern</b><small>Business Services</small></div></div>
<div class="abs foot" style="left:136px;top:1040px;width:120px">
  <p>22 Block 4/a, Park Road,<br>Riverton, CA.</p>
  <p style="margin-top:8px">+100 (0) 555 019 73<br><span class="green">contact@bluefern-mail.test</span></p>
</div>
<div class="abs fsocial"><span></span><span></span><span></span><span></span><span></span></div>

<div class="abs foot" style="left:275px;top:1012px">
  <h5>LINKS</h5>
  <ul><li>Home</li><li>About Us</li><li>Clients</li><li>Services</li><li>Contact Us</li></ul>
</div>

<div class="abs foot" style="left:415px;top:1012px;width:125px">
  <h5>LATEST NEWS</h5>
  <div style="border-top:1px solid #eee;margin-top:16px;padding-top:4px;display:flex;justify-content:space-between;font-size:5.5px;color:#aaa"><span>July 9, 2013</span><span>0</span></div>
  <p style="margin-top:12px">Lorem ipsum dolor sit amet, consectetuer adipiscing elit. Phasellus hendrerit. Pellentesque aliquet nibh nec urna. In nisi neque,</p>
  <p class="green" style="margin-top:4px">VISIT OUR BLOG</p>
</div>

<div class="abs foot" style="left:555px;top:1012px;width:130px">
  <h5>NEWSLETTER WIDGET</h5>
  <p style="margin-top:14px">Lorem ipsum dolor sit amet, consectetue adipiscing elit. Donec odio. Quis que vol utpat mattis eros. Nullam mal.</p>
  <div style="display:flex;gap:2px;margin-top:10px"><div class="input">Newsletter..</div><div class="signup">Signup</div></div>
  <p style="margin-top:8px;color:#999">Don't worry, your details are safe with us.<br>For more info. read our <span class="green">privacy policy</span></p>
</div>

<footer class="abs bottom">Copyright Bluefern Business Services Private Limited.</footer>

</body>
</html>
```